Dorwin's Coating & Renewal Letterhead Design We want to revamp out old traditional letterhead with the new logo designs that are attached. We are working on getting all our company items from vehicles, business, cards, t-shirts, letterhead to match. This should include company colors, fonts, and flow of items that we have attached below.

Industry/Entity Type

Construction Company

Font styles to use
Sans Serif
Other font styles liked:
• Bold with outline

Colors
ec1f27
ffffff

Requirements
Must have
• Company Name: Dorwin's Coating & Renewal
• Address: 4728 SW 81st Ter Halverd cove fl 39417
• Office Number: (555) 413-2986
• Email: Dorwinrenewal@mailbrook.example
• License Number: KRT8046392
Nice to have
• Company Colors: red, white, black, and grey

```html
<!DOCTYPE html>
<html lang="en">
<head>
<meta charset="utf-8">
<title>Dorwin's Coating &amp; Renewal — Letterhead</title>
<link rel="stylesheet" href="https://fonts.googleapis.com/css2?family=Lato:wght@400;700&family=Open+Sans:wght@400;600;800&display=swap">
<style>
  :root {
    --backdrop: #e6e6e7;
    --paper: #ffffff;
    --band-grey: #bdbdbf;
    --brand-red: #ef4923;
    --ink: #4f4f4f;
    --ink-dark: #333333;
    --sign-tone: #d9d9d9;
  }
  * { margin: 0; padding: 0; box-sizing: border-box; }
  html, body { width: 1040px; height: 1200px; overflow: hidden; background: var(--backdrop); }
  .letterhead {
    position: absolute; left: 53px; top: 0;
    width: 934px; height: 1200px;
    background: var(--paper);
    font-family: "Open Sans", Arial, sans-serif;
    color: var(--ink);
    overflow: hidden;
  }
  .page-shapes { position: absolute; inset: 0; }
  .contact-band {
    position: absolute; left: 0; top: 0; width: 100%; height: 33px;
    display: flex; align-items: center; justify-content: center;
    font-family: "Lato", Arial, sans-serif; font-size: 17px; color: var(--paper);
  }
  .contact-band b { font-weight: 700; }
  .brand-name {
    position: absolute; left: 95px; top: 56px;
    font-family: "Open Sans", Arial, sans-serif; font-weight: 800;
    color: var(--brand-red); text-transform: uppercase; line-height: 1.05;
  }
  .brand-name .line-main { display: block; font-size: 36px; letter-spacing: 1px; }
  .brand-name .line-sub { display: block; font-size: 18px; letter-spacing: 2.5px; }
  .letter { position: absolute; left: 88px; width: 756px; font-size: 15px; }
  .issue-date { top: 216px; }
  .recipient { top: 251px; line-height: 18px; }
  .salutation { top: 357px; }
  .letter-body { top: 380px; line-height: 27px; text-align: justify; font-size: 14.8px; letter-spacing: -0.15px; hyphens: auto; }
  .letter-body p { margin-top: 27px; }
  .letter-body p:first-child { margin-top: 27px; }
  .closing { top: 815px; }
  .signature {
    position: absolute; left: 88px; top: 852px; width: 215px; height: 28px;
    background: linear-gradient(90deg, var(--sign-tone), #ececec);
    border-radius: 14px;
  }
  .signatory { top: 892px; }
  .signatory .name { font-size: 19px; font-weight: 600; color: var(--ink-dark); }
  .signatory .role { margin-top: 4px; }
  .address-band {
    position: absolute; left: 0; bottom: 0; width: 100%; height: 38px;
    display: flex; align-items: center; justify-content: center;
    font-family: "Lato", Arial, sans-serif; font-size: 17.7px; color: var(--paper);
  }
</style>
</head>
<body>
  <main class="letterhead">
    <svg class="page-shapes" width="934" height="1200" viewBox="0 0 934 1200" aria-hidden="true">
      <rect class="band-top" x="0" y="0" width="934" height="33" fill="var(--band-grey)"/>
      <path class="corner-sweep-top" d="M0,32 H95 C45,33 0,110 0,227 Z" fill="var(--band-grey)"/>
      <path class="corner-sweep-bottom" d="M934,999 C912,1085 872,1142 800,1163 H934 Z" fill="var(--brand-red)"/>
      <rect class="band-bottom" x="0" y="1162" width="934" height="38" fill="var(--brand-red)"/>
    </svg>

    <div class="contact-band">
      <span><b>P:</b> (555) 413-2986 | <b>E:</b> Dorwinrenewal@mailbrook.example | License Number: KRT8046392</span>
    </div>

    <div class="brand-name">
      <span class="line-main">Dorwin's</span>
      <span class="line-sub">Coating &amp; Renewal</span>
    </div>

    <p class="letter issue-date">Issuing Date: May 5, 2018</p>

    <p class="letter recipient">Name Of Employee Mr. XYZABC<br>Address of Employee<br>Address Line 2 etc..</p>

    <p class="letter salutation">Dear Mr.XYZABC</p>

    <div class="letter letter-body" lang="en">
      <p>Lorem Ipsum has been the industry's standard dummy text ever since the 1500s, when an unknown printer took a galley of type and scrambled it to make a type specimen book. It has survived not only five centuries, but also the leap into electronic typesetting, remaining essentially unchanged. It was popularised in the 1960s with the release of Tessaron sheets containing Lorem Ipsum passages, and more recently with desktop publishing software like Quillon PageForge including versions of Lorem Ipsum.</p>
      <p>Lorem Ipsum is simply dummy text of the printing and typesetting industry. Lorem Ipsum has been the industry's standard dummy text ever since the 1500s, when an unknown printer took a galley of type and scrambled it to make a type specimen book.</p>
      <p>It has survived not only five centuries, but also the leap into electronic typesetting, remaining essentially unchanged. It was popularised in the 1960s with the release of Tessaron sheets containing Lorem IpsumIpsum passages.</p>
    </div>

    <p class="letter closing">Yours Sincerely</p>
    <div class="signature" role="img" aria-label="Handwritten signature of Marlow Pennick"></div>
    <div class="letter signatory">
      <p class="name">Marlow Pennick</p>
      <p class="role">Managing Director</p>
    </div>

    <div class="address-band">
      <span>DORWIN'S COATING &amp; RENEWAL : 4728 SW 81st Ter Halverd cove fl 39417</span>
    </div>
  </main>
</body>
</html>
```